Bram Keystone Homes needs a business card

We need a business card for a new company in Canada, Ontario. Our company is all about luxury contraction homes for our clients. Our product and services are custom projects design. Under the business logo that will be created, we want a slogan that will be a memorable phrase for consumers to remember us to tell their friends and relatives.

Additional infomation
- Ludovic Entrasse
- President / Ceo
-519.604.3087

Find point what luxury construction products and services can be done

We like to see colors:
- #663300
- and something other colors or color that would attract the client needs and wants

The final design should communicate leads from new or old clients that will grow our empire. Most of all, we try to work among the budget that clients want

NOTE
- we also need an icon for the business (Example: Instagram, Facebook, and Whatsapp icons)
- We want the company name to be remembered easily for clients and our distributors who would get our orders.
- we need an icon on the business cards: Facebook and Instagram.

Thanks,
Bram Keystone Homes

```html
<!DOCTYPE html>
<html lang="en">
<head>
<meta charset="utf-8">
<title>Bram Keystone Homes – Business Card</title>
<link href="https://fonts.googleapis.com/css2?family=Stardos+Stencil:wght@700&family=Lato:wght@300;400&family=Roboto:wght@700&display=swap" rel="stylesheet">
<style>
  :root {
    --brand-brown: #663300;
    --band-brown: #623100;
    --card-light: #f6f3f2;
    --page-bg: #e4e0dd;
    --text-light: #ffffff;
    --rule-light: rgba(255, 255, 255, 0.75);
  }
  * { margin: 0; padding: 0; box-sizing: border-box; }
  html, body {
    width: 1200px;
    height: 900px;
    overflow: hidden;
    background: var(--page-bg);
  }
  .business-card {
    position: absolute;
    left: 100px;
    top: 140px;
    width: 1000px;
    height: 620px;
    box-shadow: 0 18px 40px rgba(0, 0, 0, 0.18);
  }
  .card-header {
    position: absolute;
    inset: 0 0 auto 0;
    height: 311px;
    background: var(--card-light);
    text-align: center;
  }
  .company-name {
    position: absolute;
    left: 0;
    right: 0;
    top: 118px;
    font-family: "Stardos Stencil", "Georgia", serif;
    font-weight: 700;
    font-size: 60px;
    line-height: 1;
    color: var(--brand-brown);
    letter-spacing: 0.5px;
  }
  .company-tagline {
    position: absolute;
    left: 0;
    right: 0;
    top: 187px;
    font-family: "Lato", "Helvetica", sans-serif;
    font-weight: 400;
    font-size: 21px;
    letter-spacing: 1.2px;
    color: var(--brand-brown);
  }
  .card-contact {
    position: absolute;
    inset: auto 0 0 0;
    height: 309px;
    background: var(--band-brown);
    color: var(--text-light);
    text-align: center;
  }
  .contact-name {
    position: absolute;
    left: 0;
    right: 0;
    top: 42px;
    font-family: "Roboto", "Arial", sans-serif;
    font-weight: 700;
    font-size: 39px;
    letter-spacing: 0.5px;
    line-height: 1;
  }
  .contact-title {
    position: absolute;
    left: 0;
    right: 0;
    top: 88px;
    font-family: "Lato", "Helvetica", sans-serif;
    font-weight: 400;
    font-size: 27px;
    line-height: 1;
  }
  .divider {
    position: absolute;
    left: 311px;
    width: 378px;
    top: 137px;
    height: 1px;
    background: var(--rule-light);
  }
  .contact-phone {
    position: absolute;
    left: 0;
    right: 0;
    top: 154px;
    font-family: "Lato", "Helvetica", sans-serif;
    font-weight: 400;
    font-size: 40px;
    letter-spacing: 1px;
    line-height: 1;
  }
  .social-row {
    position: absolute;
    left: 307px;
    top: 217px;
    width: 386px;
    height: 42px;
  }
  .social-rule {
    position: absolute;
    top: 21px;
    height: 1px;
    width: 136px;
    background: var(--rule-light);
  }
  .social-rule.left { left: 0; }
  .social-rule.right { right: 0; }
  .social-dot {
    position: absolute;
    top: 0;
    width: 42px;
    height: 42px;
    border-radius: 50%;
    background: var(--text-light);
  }
  .social-dot.first { left: 146px; }
  .social-dot.second { left: 198px; }
</style>
</head>
<body>
  <div class="business-card">
    <header class="card-header">
      <h1 class="company-name">Bram Keystone Homes</h1>
      <p class="company-tagline">- HOME RENOVATIONS - CUSTOM PROJECT DESIGN -</p>
    </header>
    <section class="card-contact">
      <h2 class="contact-name">LUDOVIC ENTRASSE</h2>
      <p class="contact-title">President / CEO</p>
      <div class="divider"></div>
      <p class="contact-phone">519.604.3087</p>
      <div class="social-row">
        <span class="social-rule left"></span>
        <span class="social-dot first" role="img" aria-label="Social profile"></span>
        <span class="social-dot second" role="img" aria-label="Social profile"></span>
        <span class="social-rule right"></span>
      </div>
    </section>
  </div>
</body>
</html>
```